Vosley Insurance Stationery Design Project

We need a stationery design for business cards, letterhead and envelopes.

Please refer to attached brief for further information.

Industry/Entity Type

Business

```html
<!DOCTYPE html>
<html lang="en">
<head>
<meta charset="utf-8">
<title>Vosley Insurance – Business Cards</title>
<link rel="stylesheet" href="https://fonts.googleapis.com/css2?family=Source+Sans+3:ital,wght@0,400;0,600;0,700;1,400;1,600;1,700&display=swap">
<style>
  :root {
    --stage: #333333;
    --navy: #00324f;
    --orange: #ff7424;
    --grey: #c6c6c6;
    --ink: #2b2b2b;
    --white: #ffffff;
  }
  * { margin: 0; padding: 0; box-sizing: border-box; }
  html, body { width: 1200px; height: 697px; overflow: hidden; background: var(--stage); }
  body { position: relative; font-family: "Source Sans 3", sans-serif; }

  .card {
    position: absolute;
    width: 455px; height: 259px;
    border-radius: 20px;
    overflow: hidden;
  }
  .card--front { left: 74px; top: 65px; background: var(--white); }
  .card--back { left: 660px; top: 65px; background: var(--navy); }
  .card--alt { left: 361px; top: 383px; background: var(--navy); }

  .brand {
    position: absolute; left: 0; right: 0;
    text-align: center;
  }
  .brand__name { font-weight: 700; font-size: 38px; line-height: 1; letter-spacing: 0.5px; }
  .card--front .brand { top: 40px; }
  .card--front .brand__name { color: #bdbdbd; }
  .card--back .brand { top: 74px; }
  .card--alt .brand { top: 111px; }
  .card--back .brand__name, .card--alt .brand__name { color: var(--grey); }

  .tagline {
    position: absolute; top: 104px; left: 0; right: 0;
    text-align: center; color: var(--orange);
    font-style: italic; font-weight: 600; font-size: 12.8px;
  }
  .contact-row {
    position: absolute; top: 126px; left: 12px; right: 12px;
    display: flex; justify-content: space-between;
    color: var(--ink); font-size: 12.5px;
  }
  .name-band {
    position: absolute; top: 147px; left: 0; right: 0; height: 35px;
    background: var(--orange); color: var(--white);
    display: flex; align-items: center; justify-content: center; gap: 6px;
  }
  .name-band__name { font-style: italic; font-weight: 700; font-size: 15.5px; }
  .name-band__role { font-style: italic; font-size: 11px; margin-top: 3px; }
  .rule { position: absolute; left: 0; right: 0; height: 3px; background: var(--grey); }
  .card--front .rule { top: 184px; }
  .card--back .rule { top: 204px; }

  .disclosure {
    position: absolute; top: 193px; left: 6px; right: 6px;
    text-align: center; color: var(--ink);
    font-size: 10.5px; line-height: 13.8px; letter-spacing: 0.2px;
  }

  .address {
    position: absolute; left: 0; right: 0;
    text-align: center; color: var(--white);
    font-size: 15px; line-height: 15px;
  }
  .card--back .address { top: 161px; }
  .card--alt .address { top: 10px; }

  .web-band {
    position: absolute; left: 0; right: 0;
    background: var(--orange); color: var(--white);
    display: flex; align-items: center; justify-content: center;
    font-size: 14.5px; font-weight: 600;
  }
  .card--back .web-band { top: 209px; height: 30px; }
  .card--alt .top-band { position: absolute; top: 0; left: 0; right: 0; height: 50px; background: var(--orange); }
  .card--alt .web-band { top: 207px; height: 52px; font-weight: 400; }
</style>
</head>
<body>

  <section class="card card--front" aria-label="Business card front">
    <div class="brand">
      <span class="brand__name">Vosley Insurance</span>
    </div>
    <p class="tagline">Business and Life Insurance Brokers and Advisers</p>
    <p class="contact-row">
      <span>T : (02) 8140 3271</span>
      <span>M : 0491 562 018</span>
      <span>F : (02) 9430 6195</span>
      <span>E : dmarlow@vsn.net.au</span>
    </p>
    <div class="name-band">
      <span class="name-band__name">Dean Marlow,</span>
      <span class="name-band__role">Director</span>
    </div>
    <div class="rule"></div>
    <p class="disclosure">
      Authorised Representative No. 402183<br>
      Harbourline Cover Australia Pty Limited AFSL 317862 Harbourline Cover Financial<br>
      Services Pty Ltd and its advisers are members of Kestrel Financial Advisers and<br>
      Authorised Representatives of Tallis Advice Group Pty Ltd AFSL 291574
    </p>
  </section>

  <section class="card card--back" aria-label="Business card back">
    <div class="brand">
      <span class="brand__name">Vosley Insurance</span>
    </div>
    <p class="address">
      Level 2, 18 Carrow St., Northgate NSW 2065<br>
      PO Box 417., Northgate NSW 2064
    </p>
    <div class="rule"></div>
    <p class="web-band">www.vosleyinsurance.com.au</p>
  </section>

  <section class="card card--alt" aria-label="Business card back, alternate">
    <div class="top-band"></div>
    <p class="address">
      Level 2, 18 Carrow St., Northgate NSW 2065<br>
      PO Box 417., Northgate NSW 2064
    </p>
    <div class="brand">
      <span class="brand__name">Vosley Insurance</span>
    </div>
    <p class="web-band">www.vosleyinsurance.com.au</p>
  </section>

</body>
</html>
```